Business Card Design

We need a design for business cards for our company. We have a logo. We teach EMT's and we are based out of Virginia. The information that will need to add would be, name, title, phone number, email, address. On the back of the business card would be "We help you, help others"

Target Market(s)

People that want to become EMT's

Colors

Designer to choose colors to be used in the design.

Requirements
Must have
• company logo

```html
<!DOCTYPE html>
<html lang="en">
<head>
<meta charset="utf-8">
<title>Rescue Ready Academy – Business Card</title>
<link href="https://fonts.googleapis.com/css2?family=Montserrat:wght@400;600;700&display=swap" rel="stylesheet">
<style>
  :root {
    --page-bg: #2a2d31;
    --card-navy: #1f2a33;
    --brand-red: #c61f2e;
    --brand-red-text: #e0283a;
    --silver: #a7aeb4;
    --white: #ffffff;
    --soft-white: #f3d9dc;
  }
  * { box-sizing: border-box; margin: 0; padding: 0; }
  html, body {
    width: 1200px; height: 900px; overflow: hidden;
    background: var(--page-bg);
    font-family: "Montserrat", sans-serif;
  }
  .sheet {
    width: 1200px; height: 900px;
    display: flex; flex-direction: column;
    align-items: center; justify-content: center; gap: 28px;
  }
  .card {
    position: relative;
    width: 700px; height: 400px;
    background: var(--card-navy);
    overflow: hidden;
    box-shadow: 0 10px 30px rgba(0,0,0,0.35);
  }
  .card__brand {
    position: absolute; left: 0; right: 0; top: 0; bottom: 120px;
    display: flex; align-items: center; justify-content: center; gap: 18px;
  }
  .brand-dot {
    width: 34px; height: 34px; border-radius: 50%;
    background: var(--brand-red-text);
  }
  .brand-name {
    font-weight: 700; font-size: 40px; letter-spacing: 1px;
    color: var(--brand-red-text); text-transform: uppercase;
  }
  .card__band {
    position: absolute; left: 0; right: 0; bottom: 0; height: 120px;
    background: var(--brand-red);
    display: flex; align-items: center; justify-content: space-between;
    padding: 0 40px;
    color: var(--white);
  }
  .person__name {
    font-weight: 700; font-size: 24px; letter-spacing: 0.5px; text-transform: uppercase;
  }
  .person__title {
    font-weight: 400; font-size: 17px; color: var(--soft-white); margin-top: 4px;
  }
  .contact { list-style: none; text-align: right; }
  .contact li {
    display: flex; align-items: center; justify-content: flex-end; gap: 12px;
    font-size: 20px; font-weight: 400; line-height: 1.6;
  }
  .contact svg { width: 20px; height: 20px; flex: none; }
  .card--back .card__band { justify-content: center; }
  .tagline {
    font-weight: 700; font-size: 22px; letter-spacing: 4px; text-transform: uppercase;
  }
</style>
</head>
<body>
<main class="sheet">
  <section class="card card--front" aria-label="Card front">
    <div class="card__brand">
      <span class="brand-dot"></span>
      <span class="brand-name">Rescue Ready Academy</span>
    </div>
    <div class="card__band">
      <div class="person">
        <div class="person__name">Daniel Reyes</div>
        <div class="person__title">Sales Manager</div>
      </div>
      <ul class="contact">
        <li>555-210-4478
          <svg viewBox="0 0 20 20" aria-hidden="true"><circle cx="10" cy="10" r="8.5" fill="none" stroke="#fff" stroke-width="1.5"/><path d="M7 5.5l1.6 2.4-1 1.2a6 6 0 0 0 3.3 3.3l1.2-1 2.4 1.6-.8 1.6c-3.8.2-8.2-4.2-8-8z" fill="#fff"/></svg>
        </li>
        <li>hello@rescueready.com
          <svg viewBox="0 0 20 20" aria-hidden="true"><rect x="2" y="4.5" width="16" height="11" fill="none" stroke="#fff" stroke-width="1.5"/><path d="M2.5 5l7.5 6 7.5-6" fill="none" stroke="#fff" stroke-width="1.5"/></svg>
        </li>
      </ul>
    </div>
  </section>

  <section class="card card--back" aria-label="Card back">
    <div class="card__brand">
      <span class="brand-dot"></span>
      <span class="brand-name">Rescue Ready Academy</span>
    </div>
    <div class="card__band">
      <p class="tagline">We help you, help others</p>
    </div>
  </section>
</main>
</body>
</html>
```